Small Business Broker Business Card Design

A business card design for a small business brokerage, which is a financial service, not unlike real estate brokerage, but for small businesses such as laundromats, pizza shops, restaurants, cleaners etc. The designs should all be simple, more conservative in nature, using the colors and font of the logo. Again, think real estate Brokerage as a business context
Contact Information for Business Card
Name: Glen R. Harlow. Title: Small Business Advisor. Email: g.harlow@bayfieldcapitalworks.example. Mobile: (555) 274-3918. Office: (555) 806-2147. www.bayfieldcapitalworks.example

```html
<!DOCTYPE html>
<html lang="en">
<head>
<meta charset="utf-8">
<title>Bayfield Capital Works – Business Card</title>
<link rel="stylesheet" href="https://fonts.googleapis.com/css2?family=Montserrat:wght@600;700&family=Arimo:wght@400&display=swap">
<style>
  :root {
    --bg: #16181c;
    --navy: #1a2f63;
    --navy-light: #213b78;
    --navy-dark: #152756;
    --green: #7dc242;
    --white: #ffffff;
    --rule: rgba(255,255,255,0.85);
  }
  * { box-sizing: border-box; margin: 0; padding: 0; }
  html, body { width: 1200px; height: 963px; overflow: hidden; background: var(--bg); }
  .canvas {
    width: 1200px; height: 963px;
    display: flex; flex-direction: column; align-items: center; justify-content: center; gap: 56px;
  }
  .card {
    position: relative; width: 700px; height: 400px; border-radius: 26px;
    background: radial-gradient(ellipse at 55% 45%, var(--navy-light) 0%, var(--navy) 55%, var(--navy-dark) 100%);
    color: var(--white); overflow: hidden;
    box-shadow: 0 18px 40px rgba(0,0,0,0.55);
  }
  .brand-name {
    font-family: "Montserrat", sans-serif; font-weight: 700; letter-spacing: 0.04em;
    text-transform: uppercase; color: var(--white); white-space: nowrap;
  }
  .brand-tagline {
    font-family: "Montserrat", sans-serif; font-weight: 600; letter-spacing: 0.08em;
    text-transform: uppercase; color: var(--green); white-space: nowrap;
  }

  /* front */
  .holder { position: absolute; left: 52px; top: 66px; }
  .holder-name {
    font-family: "Montserrat", sans-serif; font-weight: 700; font-size: 30px;
    letter-spacing: 0.03em; text-transform: uppercase;
  }
  .holder-title {
    font-family: "Arimo", sans-serif; font-size: 19px; color: var(--green); margin-top: 4px;
  }
  .divider { position: absolute; left: 52px; right: 52px; top: 150px; height: 1.5px; background: var(--rule); }
  .phones { position: absolute; left: 52px; top: 172px; list-style: none; }
  .contact-row {
    display: flex; align-items: center; gap: 12px;
    font-family: "Arimo", sans-serif; font-size: 19px; line-height: 30px;
  }
  .contact-row svg { width: 18px; height: 18px; flex: none; }
  .brand-front { position: absolute; right: 52px; top: 190px; text-align: right; }
  .brand-front .brand-line { display: flex; align-items: center; justify-content: flex-end; gap: 12px; }
  .brand-front .brand-name { font-size: 20px; }
  .brand-front .brand-tagline { font-size: 9.5px; margin-top: 5px; }
  .brand-mark { width: 16px; height: 16px; background: var(--green); }
  .online { position: absolute; right: 52px; bottom: 46px; list-style: none; }
  .online .contact-row { justify-content: flex-end; font-size: 18px; }

  /* back */
  .brand-back { position: absolute; right: 48px; top: 56px; text-align: left; }
  .brand-back .brand-name { font-size: 24px; }
  .brand-back .brand-tagline { font-size: 11px; margin-top: 6px; }
</style>
</head>
<body>
<main class="canvas">
  <section class="card card-front" aria-label="Business card front">
    <div class="holder">
      <h1 class="holder-name">Glen R. Harlow</h1>
      <p class="holder-title">Small Business Advisor</p>
    </div>
    <div class="divider"></div>
    <ul class="phones">
      <li class="contact-row">
        <svg viewBox="0 0 24 24" fill="none" stroke="var(--green)" stroke-width="2.2" aria-hidden="true"><path d="M5 3h4l2 5-2.5 1.5a11 11 0 0 0 6 6L16 13l5 2v4a2 2 0 0 1-2 2A16 16 0 0 1 3 5a2 2 0 0 1 2-2z"/></svg>
        <span>(555) 806-2147</span>
      </li>
      <li class="contact-row">
        <svg viewBox="0 0 24 24" fill="none" stroke="var(--green)" stroke-width="2.2" aria-hidden="true"><rect x="6" y="2" width="12" height="20" rx="2"/><line x1="11" y1="18" x2="13" y2="18"/></svg>
        <span>(555) 274-3918</span>
      </li>
    </ul>
    <div class="brand-front">
      <div class="brand-line"><span class="brand-mark"></span><span class="brand-name">Bayfield Capital Works, Inc</span></div>
      <p class="brand-tagline">Trusted guidance to buy or sell a main street firm</p>
    </div>
    <ul class="online">
      <li class="contact-row">
        <svg viewBox="0 0 24 24" fill="none" stroke="var(--green)" stroke-width="2" aria-hidden="true"><rect x="3" y="5" width="18" height="14" rx="1"/><path d="M3 6l9 7 9-7"/></svg>
        <span>g.harlow@bayfieldcapitalworks.example</span>
      </li>
      <li class="contact-row">
        <svg viewBox="0 0 24 24" fill="none" stroke="var(--green)" stroke-width="2" aria-hidden="true"><circle cx="12" cy="12" r="9"/><path d="M3 12h18M12 3c3 3 3 15 0 18M12 3c-3 3-3 15 0 18"/></svg>
        <span>www.bayfieldcapitalworks.example</span>
      </li>
    </ul>
  </section>

  <section class="card card-back" aria-label="Business card back">
    <div class="brand-back">
      <p class="brand-name">Bayfield Capital Works, Inc</p>
      <p class="brand-tagline">Trusted guidance to buy or sell a main street firm</p>
    </div>
  </section>
</main>
</body>
</html>
```